Home Security Company Business Card

Looking for a eye catching business card that is non traditional and stands out but yet still looks professional. It should include all the pertinent information such as name, title, address, telephone, e-mail, website address should definitely stand out and then finally the logo.

Target Market(s)

Residential and Commercial accounts mostly upscale accounts

Industry/Entity Type

Security

Contact Information for Business Card

Name
Title
Address
Office #
Cell #
E-mail
Website

Font styles to use
Serif
Sans Serif

Requirements
Must have
• Logo, two sided color configuration
Nice to have
• You decide
Should not have
• There really aren't any.

```html
<!DOCTYPE html>
<html lang="en">
<head>
<meta charset="utf-8">
<title>Havenmark Security Systems – Business Card</title>
<link rel="stylesheet" href="https://fonts.googleapis.com/css2?family=Open+Sans:wght@400;600;700&display=swap">
<style>
  :root {
    --stage: #e9e6e1;
    --paper: #ffffff;
    --charcoal: #2a2a2a;
    --charcoal-deep: #1e1e1e;
    --maroon: #7f1416;
    --gold: #f2c043;
    --ink: #3a3a3a;
    --ink-soft: #555555;
    --white: #ffffff;
  }
  * { box-sizing: border-box; margin: 0; padding: 0; }
  html, body {
    width: 1200px; height: 900px; overflow: hidden;
    background: var(--stage);
    font-family: "Open Sans", Arial, sans-serif;
  }
  .sheet {
    position: relative; width: 1200px; height: 900px;
    display: flex; flex-direction: column; align-items: center;
    justify-content: center; gap: 50px;
  }
  .card {
    position: relative; width: 700px; height: 400px; overflow: hidden;
    box-shadow: 0 6px 18px rgba(0,0,0,.18);
  }

  /* Shared wordmark: one font, one weight, one colour */
  .brand { display: flex; align-items: center; gap: 14px; }
  .brand__mark { width: 20px; height: 20px; background: var(--gold); flex: none; }
  .brand__name {
    font-family: "Open Sans", Arial, sans-serif;
    font-weight: 600; line-height: 1.25;
  }

  /* Back side */
  .card--back {
    background: linear-gradient(160deg, var(--charcoal) 0%, var(--charcoal-deep) 100%);
    display: flex; align-items: center; justify-content: center;
  }
  .card--back .brand__name { color: var(--white); font-size: 28px; }

  /* Front side */
  .card--front { background: var(--paper); }
  .card__bands { position: absolute; inset: 0; width: 700px; height: 400px; }
  .holder { position: absolute; left: 72px; top: 26px; }
  .holder__name { font-size: 21px; font-weight: 700; color: var(--maroon); }
  .holder__first { color: var(--gold); }
  .holder__title { font-size: 15px; color: var(--ink-soft); margin-top: -2px; }
  .contact {
    position: absolute; left: 40px; top: 140px;
    font-size: 16.5px; font-style: normal; color: var(--ink); line-height: 1.35;
  }
  .contact__address { margin-bottom: 10px; }
  .contact__list { list-style: none; }
  .contact__list li { display: flex; align-items: center; gap: 8px; }
  .contact__icon { width: 12px; height: 12px; flex: none; }
  .card--front .brand { position: absolute; left: 380px; top: 150px; }
  .card--front .brand__name { color: var(--maroon); font-size: 22px; max-width: 250px; }
</style>
</head>
<body>
<main class="sheet">

  <section class="card card--back" aria-label="Business card, back">
    <div class="brand">
      <span class="brand__mark" aria-hidden="true"></span>
      <p class="brand__name">Havenmark Security Systems Inc.</p>
    </div>
  </section>

  <section class="card card--front" aria-label="Business card, front">
    <svg class="card__bands" viewBox="0 0 700 400" aria-hidden="true">
      <polygon points="14,0 30,0 10,40 0,40 0,26" fill="var(--gold)"/>
      <polygon points="36,0 64,0 44,40 16,40" fill="var(--maroon)"/>
      <polygon points="0,318 310,318 296,348 0,348" fill="var(--gold)"/>
      <polygon points="318,330 700,330 700,400 286,400" fill="var(--maroon)"/>
    </svg>

    <header class="holder">
      <h1 class="holder__name"><span class="holder__first">Daniel</span> Reyes</h1>
      <p class="holder__title">Managing Director</p>
    </header>

    <address class="contact">
      <p class="contact__address">12345, Address Goes Here<br>Country Name, 123456.</p>
      <ul class="contact__list">
        <li>
          <svg class="contact__icon" viewBox="0 0 12 12" aria-hidden="true"><path d="M1 4 Q6 0 11 4 L9 6 L8 4.5 H4 L3 6 Z M2 7 H10 V11 H2 Z" fill="var(--maroon)"/></svg>
          044-123 456 789
        </li>
        <li>
          <svg class="contact__icon" viewBox="0 0 12 12" aria-hidden="true"><rect x="3" y="0.5" width="6" height="11" rx="1" fill="none" stroke="var(--maroon)" stroke-width="1.4"/></svg>
          044-123 456 789
        </li>
        <li>
          <svg class="contact__icon" viewBox="0 0 12 12" aria-hidden="true"><rect x="0.5" y="2" width="11" height="8" fill="var(--maroon)"/><path d="M0.5 2 L6 6.5 L11.5 2" fill="none" stroke="var(--white)" stroke-width="1"/></svg>
          info@webname.com
        </li>
        <li>
          <svg class="contact__icon" viewBox="0 0 12 12" aria-hidden="true"><path d="M5 7 L7 5 M4 5.5 L2.5 7 A1.8 1.8 0 0 0 5 9.5 L6.5 8 M8 6.5 L9.5 5 A1.8 1.8 0 0 0 7 2.5 L5.5 4" fill="none" stroke="var(--maroon)" stroke-width="1.4" stroke-linecap="round"/></svg>
          www.websitename.com
        </li>
      </ul>
    </address>

    <div class="brand">
      <span class="brand__mark" aria-hidden="true"></span>
      <p class="brand__name">Havenmark Security Systems Inc.</p>
    </div>
  </section>

</main>
</body>
</html>
```